Telecommunications/Power civil contractor needs business card design

Were a new telecommunications/power underground civil contractor that is looking for a new business card design. Our company colours are silver or grey and orange. Feel free to use the white background logo or the black background logo.

Target Market(s)

Local contractors, utility companies, private sector mining/energy companies, developers.

Industry/Entity Type

Telecommunications

Contact Information for Business Card

Each card will need the following info:
Persons name:
Title:
E-mail:
Phone number:
Shop Address:
Mailing Address:

Requirements
Must have
• Each card will need the following info:
• Persons name:
• Title:
• E-mail:
• Phone number:
• Shop Address:
• Mailing Address:

```html
<!DOCTYPE html>
<html lang="en">
<head>
<meta charset="utf-8">
<title>Tamlin Civil Works Inc – Business Card</title>
<link href="https://fonts.googleapis.com/css2?family=Lato:wght@400;700;900&display=swap" rel="stylesheet">
<style>
  :root {
    --stage: #1b1b1c;
    --card-top: #2c2c2e;
    --card-bottom: #161617;
    --orange: #e8601c;
    --white: #f2f2f2;
    --silver: #c9c9c9;
    --grey-text: #d8d8d8;
  }
  * { box-sizing: border-box; margin: 0; padding: 0; }
  html, body {
    width: 1200px;
    height: 873px;
    overflow: hidden;
    background: var(--stage);
    font-family: "Lato", sans-serif;
  }
  .canvas {
    position: relative;
    width: 1200px;
    height: 873px;
  }
  .business-card {
    position: absolute;
    left: 200px;
    top: 208px;
    width: 800px;
    height: 457px;
    border-radius: 20px;
    overflow: hidden;
    box-shadow: 0 18px 40px rgba(0,0,0,0.55);
  }
  .card-texture {
    position: absolute;
    inset: 0;
    background: linear-gradient(150deg, var(--card-top) 0%, #222224 45%, var(--card-bottom) 100%);
  }
  .holder {
    position: absolute;
    right: 56px;
    top: 46px;
    text-align: right;
  }
  .holder-name {
    color: var(--white);
    font-weight: 700;
    font-size: 27px;
    letter-spacing: 0.3px;
  }
  .holder-title {
    color: var(--grey-text);
    font-size: 17px;
    margin-top: 6px;
  }
  .company {
    position: absolute;
    left: 56px;
    top: 120px;
    display: flex;
    align-items: center;
    gap: 16px;
  }
  .company-dot {
    width: 54px;
    height: 54px;
    border-radius: 50%;
    background: var(--orange);
  }
  .company-name {
    color: var(--orange);
    font-weight: 900;
    font-size: 30px;
    letter-spacing: 1px;
    line-height: 1.05;
  }
  .contact-list {
    position: absolute;
    left: 56px;
    bottom: 46px;
    list-style: none;
  }
  .contact-item {
    display: flex;
    align-items: center;
    gap: 14px;
    color: var(--grey-text);
    font-size: 19px;
    height: 38px;
  }
  .contact-icon {
    width: 20px;
    height: 20px;
    flex: none;
    fill: var(--orange);
  }
  .contact-label {
    color: var(--orange);
    font-size: 17px;
    margin-left: 8px;
  }
</style>
</head>
<body>
<main class="canvas">
  <section class="business-card">
    <div class="card-texture" role="img" aria-label="Dark grey low-poly faceted background texture"></div>

    <header class="holder">
      <p class="holder-name">Daniel Varrow</p>
      <p class="holder-title">Chief Operating Officer</p>
    </header>

    <div class="company">
      <span class="company-dot"></span>
      <p class="company-name">TAMLIN CIVIL<br>WORKS INC</p>
    </div>

    <ul class="contact-list">
      <li class="contact-item">
        <svg class="contact-icon" viewBox="0 0 24 24" aria-hidden="true"><path d="M6.6 10.8a15.1 15.1 0 0 0 6.6 6.6l2.2-2.2a1 1 0 0 1 1-.25 11.4 11.4 0 0 0 3.6.57 1 1 0 0 1 1 1V20a1 1 0 0 1-1 1A17 17 0 0 1 3 4a1 1 0 0 1 1-1h3.5a1 1 0 0 1 1 1c0 1.25.2 2.45.57 3.57a1 1 0 0 1-.25 1z"/></svg>
        <span>412-555-0148</span>
      </li>
      <li class="contact-item">
        <svg class="contact-icon" viewBox="0 0 24 24" aria-hidden="true"><path d="M2 5h20v14H2z M4 7v.5l8 5 8-5V7l-8 5z" fill-rule="evenodd"/></svg>
        <span>enquiries@tamlincivilworks.com</span>
      </li>
      <li class="contact-item">
        <svg class="contact-icon" viewBox="0 0 24 24" aria-hidden="true"><path d="M12 2a7 7 0 0 0-7 7c0 5 7 13 7 13s7-8 7-13a7 7 0 0 0-7-7zm0 9.5A2.5 2.5 0 1 1 12 6.5a2.5 2.5 0 0 1 0 5z"/></svg>
        <span>48 Harlow Drive, Cedarville, PA 15230<span class="contact-label">(Shop Address)</span></span>
      </li>
      <li class="contact-item">
        <svg class="contact-icon" viewBox="0 0 24 24" aria-hidden="true"><path d="M12 2a7 7 0 0 0-7 7c0 5 7 13 7 13s7-8 7-13a7 7 0 0 0-7-7zm0 9.5A2.5 2.5 0 1 1 12 6.5a2.5 2.5 0 0 1 0 5z"/></svg>
        <span>#1920 Brenner Avenue, Oakhurst, New York<span class="contact-label">(Mailling Address)</span></span>
      </li>
    </ul>
  </section>
</main>
</body>
</html>
```